Business Card for Field Lotus-Eco Friendly Organic Clothing Brand

We are looking for an amazing business card for our eco friendly, organic clothing brand. We are thinking maybe a business card with a peel off sticker on the back, since our hanging clothing tag is a peel off sticker on the back. I will attach our hang tag so we can make sure we stay in line with our design. I've also attached a bag we are doing because I do like the scattered emblem look as well.

```html
<!DOCTYPE html>
<html lang="en">
<head>
<meta charset="utf-8">
<title>Field Lotus – Business Card</title>
<link rel="stylesheet" href="https://fonts.googleapis.com/css2?family=Open+Sans:wght@400;600;700&display=swap">
<style>
  :root {
    --backdrop: #8e8e8c;
    --ink: #000000;
    --card-dark: #0b0b0a;
    --pattern-dark: #1d1f19;
    --pattern-mid: #2b2d24;
    --gold-light: #f0dc97;
    --gold-mid: #dcb656;
    --gold-deep: #c4952d;
    --gold-text: #e2bd4f;
  }
  * { box-sizing: border-box; margin: 0; padding: 0; }
  html, body {
    width: 1200px; height: 900px; overflow: hidden;
    background: var(--backdrop);
    font-family: "Open Sans", Arial, sans-serif;
  }
  .canvas { position: relative; width: 1200px; height: 900px; }

  .card {
    position: absolute; left: 285px; width: 630px; height: 360px;
    overflow: hidden; box-shadow: 0 6px 18px rgba(0,0,0,.25);
  }
  .card--back { top: 50px; }
  .card--front { top: 470px; display: flex; }

  /* Back side */
  .back-pattern {
    position: absolute; inset: 0;
    background: radial-gradient(ellipse at 50% 50%, var(--pattern-mid), var(--pattern-dark) 75%);
  }
  .back-badge {
    position: absolute; left: 220px; top: 40px;
    display: flex; align-items: center; gap: 14px;
    padding: 12px 20px; border: 2px solid var(--gold-text); background: var(--card-dark);
  }
  .back-badge .mark-square { width: 34px; height: 34px; border: 2px solid var(--gold-text); }
  .back-badge .brand { font-size: 22px; }
  .back-banner {
    position: absolute; left: 40px; right: 40px; top: 180px; height: 92px;
    border: 3px solid var(--gold-text); background: rgba(11,11,10,.85);
    display: flex; align-items: center; justify-content: center;
  }
  .back-banner .brand { font-size: 54px; letter-spacing: 1px; }

  .brand { color: var(--gold-text); font-weight: 700; line-height: 1; }
  .brand-url { color: var(--gold-text); font-size: 10px; font-weight: 400; margin-top: 4px; }

  /* Front side */
  .front-brand-side {
    width: 52%; background: var(--card-dark);
    display: flex; align-items: center; justify-content: center;
  }
  .front-logo {
    display: flex; align-items: center; gap: 14px;
    padding: 14px 18px; border: 2px solid var(--gold-text);
  }
  .front-logo .mark-square { width: 40px; height: 40px; border: 2px solid var(--gold-text); }
  .front-logo .brand { font-size: 28px; }

  .front-contact-side {
    width: 48%;
    background: linear-gradient(180deg, var(--gold-light), var(--gold-mid) 55%, var(--gold-deep));
    padding: 72px 28px 0 20px; text-align: right; color: var(--ink);
  }
  .person-name { font-size: 21px; font-weight: 700; line-height: 1.1; }
  .person-role { font-size: 15px; margin-bottom: 14px; }
  .address { font-size: 15px; line-height: 1.3; margin-bottom: 16px; }
  .contact-list { list-style: none; font-size: 15px; line-height: 1.45; }
  .contact-list li { display: flex; justify-content: flex-end; align-items: center; gap: 10px; }
  .contact-list svg { width: 12px; height: 12px; fill: var(--ink); flex: none; }
</style>
</head>
<body>
<main class="canvas">

  <section class="card card--back" aria-label="Card back">
    <div class="back-pattern" role="img" aria-label="Scattered gold emblem pattern with peace signs, hearts and words like Namaste, Om, Live, inspire and Peace on dark olive"></div>
    <div class="back-badge">
      <span class="mark-square"></span>
      <div>
        <div class="brand">Field Lotus</div>
        <div class="brand-url">www.fieldlotus.com</div>
      </div>
    </div>
    <div class="back-banner">
      <span class="brand">Field Lotus</span>
    </div>
  </section>

  <section class="card card--front" aria-label="Card front">
    <div class="front-brand-side">
      <div class="front-logo">
        <span class="mark-square"></span>
        <div>
          <div class="brand">Field Lotus</div>
          <div class="brand-url">www.fieldlotus.com</div>
        </div>
      </div>
    </div>
    <div class="front-contact-side">
      <p class="person-name">Jonathan Smith</p>
      <p class="person-role">Managing Director</p>
      <p class="address">12345, Address Goes Here<br>Country Name, 123456.</p>
      <ul class="contact-list">
        <li>044-123 456 789
          <svg viewBox="0 0 24 24"><path d="M6.6 10.8a15 15 0 006.6 6.6l2.2-2.2c.3-.3.7-.4 1-.2 1.1.4 2.3.6 3.6.6.6 0 1 .4 1 1V20c0 .6-.4 1-1 1A17 17 0 013 4c0-.6.4-1 1-1h3.5c.6 0 1 .4 1 1 0 1.3.2 2.5.6 3.6.1.3 0 .7-.2 1z"/></svg>
        </li>
        <li>info@webname.com
          <svg viewBox="0 0 24 24"><path d="M2 5h20v14H2z M2 5l10 8 10-8" fill="none" stroke="#000" stroke-width="2.5"/></svg>
        </li>
        <li>www.websitename.com
          <svg viewBox="0 0 24 24"><circle cx="12" cy="12" r="10"/></svg>
        </li>
      </ul>
    </div>
  </section>

</main>
</body>
</html>
```